Equipment Finance Specialist I work with companies who need the funds to buy their equipment

I would like a business card that stands out on the shelves. I want to be able to hand it to someone and say WOW. This card should have my logo.
You can put color into it I am very open on design and color

What my company does is we deal with dealerships that sell equipment such as Dump Trucks garbage trucks tractors trailers. Customers get referred to us and depending on their time in business we will ask for the following items

Companies that have been in business for more than two years we have a credit application program up to 250K . With this program we need the following items Credit application filled out(which is what I would like to be able for the customer to click on my website to get.) as well as three current month bank statements.

Deals over 250k we will need the following items

2 years business tax returns
2 years personal tax returns
Profit & Loss statement
Personal Financial Statement

what we do
100% FINANCING
SEASONAL PAYMENTS
LOAN BALLOON PAYMENTS
TRAC LEASING
LOW-INTEREST REFINANCING RATES
DEBT CONSOLIDATION

We specialize in creative financing solutions and offer a variety of reliable, flexible and expandable lending choices.

Target Market(s)

Trucking Companies

Industry/Entity Type

Trucking Company

Contact Information for Business Card

* $250,000 Application only Program
* Loans from $30,000 to 5,000,000
* Competitive Interest Rates

Font styles to use
Serif
Sans Serif

Colors

Designer to choose colors to be used in the design.

Requirements
Must have
• On the back of the card.
• * $250,000 Application only Program
• * Loans from $30,000 to 5,000,000
• My name, email, website. address
• * Competitive Interest Rates
• * 100% Financing
Nice to have
• I want my logo to pop on the card
• My logo is the great one I would like to use
Should not have
• I am up for your creativity as well

```html
<!DOCTYPE html>
<html lang="en">
<head>
<meta charset="utf-8">
<title>Summit Lending – Business Card</title>
<link href="https://fonts.googleapis.com/css2?family=Open+Sans:wght@400;600;700;800&display=swap" rel="stylesheet">
<style>
  :root {
    --navy: #15306f;
    --red: #c81f46;
    --red-light: #cf2650;
    --white: #ffffff;
    --ink: #4a4a4a;
    --stage: #2b2b2b;
  }
  * { box-sizing: border-box; margin: 0; padding: 0; }
  html, body { width: 1200px; height: 892px; overflow: hidden; }
  body {
    background: var(--stage);
    font-family: "Open Sans", Arial, sans-serif;
    position: relative;
  }
  .card {
    position: absolute;
    left: 250px;
    width: 700px;
    height: 400px;
    overflow: hidden;
    border-radius: 4px;
  }
  /* Back side */
  .card--back {
    top: 30px;
    background: linear-gradient(160deg, var(--red-light), var(--red));
    color: var(--white);
  }
  .brand {
    position: absolute;
    display: flex;
    align-items: center;
    gap: 14px;
    color: var(--navy);
    font-weight: 800;
    letter-spacing: 1px;
    text-transform: uppercase;
    white-space: nowrap;
  }
  .brand__dot { border-radius: 50%; background: var(--navy); flex: none; }
  .card--back .brand { left: 50%; top: 108px; transform: translateX(-50%); font-size: 36px; }
  .card--back .brand__dot { width: 90px; height: 90px; }
  .offer {
    position: absolute;
    left: 0; right: 0;
    bottom: 62px;
    text-align: center;
    font-size: 19px;
    line-height: 1.45;
  }
  /* Front side */
  .card--front { top: 462px; background: var(--white); }
  .card--front .brand { left: 50%; top: 58px; transform: translateX(-50%); font-size: 34px; }
  .card--front .brand__dot { width: 66px; height: 66px; }
  .wave { position: absolute; inset: 0; }
  .details {
    position: absolute;
    left: 40px;
    right: 30px;
    top: 160px;
    display: flex;
    align-items: center;
    white-space: nowrap;
  }
  .details__block { padding: 0 20px; font-size: 15px; line-height: 1.4; color: var(--ink); }
  .details__block:first-child { padding-left: 0; }
  .details__rule { width: 2px; height: 44px; background: var(--navy); flex: none; }
  .person__name { color: var(--navy); font-weight: 800; font-size: 23px; line-height: 1.1; }
  .person__role { color: var(--red); font-size: 16px; text-transform: uppercase; }
  .website {
    position: absolute;
    right: 40px;
    bottom: 32px;
    color: var(--white);
    font-size: 17px;
  }
</style>
</head>
<body>

  <section class="card card--back" aria-label="Card back">
    <div class="brand"><span class="brand__dot"></span>Summit Lending</div>
    <p class="offer">
      $250,000 Application only Program • Loans from $30,000 to 5,000,000<br>
      Competitive Interest Rates • 100% Financing
    </p>
  </section>

  <section class="card card--front" aria-label="Card front">
    <svg class="wave" viewBox="0 0 700 400" preserveAspectRatio="none" aria-hidden="true">
      <path d="M0 355 C200 340 400 305 520 270 C600 248 650 240 700 236 L700 400 L0 400 Z" fill="var(--navy)"/>
      <path d="M0 335 C160 325 320 308 470 262 C330 318 170 340 0 350 Z" fill="var(--red)"/>
    </svg>

    <div class="brand"><span class="brand__dot"></span>Summit Lending</div>

    <div class="details">
      <div class="details__block person">
        <div class="person__name">MARK ELLISON</div>
        <div class="person__role">President</div>
      </div>
      <span class="details__rule"></span>
      <div class="details__block">
        2190 Harbor View Road<br>
        Oak Hill, NY 11020
      </div>
      <span class="details__rule"></span>
      <div class="details__block">
        P: 555 0142 7788<br>
        mark@summitlending.com
      </div>
    </div>

    <div class="website">www.summitlending.com</div>
  </section>

</body>
</html>
```